KTWG application splash screen

We need a 1024x768 image for use as an application splash screen.
The image will be displayed full screen on an 10 inch industrial PC 1024x768 screen while our application is launching. The image should convey that the application is "Waiting for connection to Wi-Fi access point..." and include a graphic of the industrial PC connected to the access point via an Ethernet cable. A list of troubleshooting steps should be included at the bottom of the image. The troubleshooting steps should not be the main focus of the image and should be shown in a smaller font (but still readable at 1024x768 displayed on a 10 inch screen).
I will include a mock up of the general idea of what we are looking for as well as image files for the industrial PC, a screenshot of our application to show on the PC's screen and the AP.
For general look and feel and a sense of corporate branding please review our website https://marrowgatesoilworks.example/. The splash screen should reflect corporate branding.
Target Market(s)
Users of our application
Industry/Entity Type
Agriculture
Look and feel

```html
<!DOCTYPE html>
<html lang="en">
<head>
<meta charset="utf-8">
<title>KTWG – Waiting for Wi-Fi access point</title>
<link href="https://fonts.googleapis.com/css2?family=Baloo+2:wght@500;600&family=Poppins:wght@400;500;600&display=swap" rel="stylesheet">
<style>
  :root {
    --brand-green: #2bb673;
    --brand-green-dark: #24a364;
    --paper: #ffffff;
    --ink: #111111;
    --device-dark: #2a2a2a;
    --device-mid: #4a4a4a;
    --ap-light: #f4f4f4;
    --ap-shade: #dcdcdc;
  }
  html, body {
    margin: 0;
    padding: 0;
    width: 1200px;
    height: 900px;
    overflow: hidden;
    background: var(--brand-green);
  }
  .splash {
    position: relative;
    width: 1024px;
    height: 768px;
    transform: scale(1.171875);
    transform-origin: 0 0;
    background: var(--brand-green);
    font-family: "Poppins", sans-serif;
    color: var(--paper);
  }
  .backdrop {
    position: absolute;
    inset: 0;
  }
  .headline {
    position: absolute;
    left: 40px;
    top: 28px;
    width: 600px;
    margin: 0;
    text-align: center;
    font-family: "Baloo 2", sans-serif;
    font-weight: 500;
    font-size: 64px;
    line-height: 68px;
    color: var(--paper);
  }
  .cab-computer {
    position: absolute;
    left: 78px;
    top: 331px;
    width: 270px;
    height: 209px;
    border-radius: 14px;
    background: linear-gradient(160deg, var(--device-mid), var(--device-dark));
  }
  .cab-computer::after {
    content: "";
    position: absolute;
    left: 24px;
    top: 18px;
    width: 222px;
    height: 165px;
    background: linear-gradient(180deg, #f2f6f3, #d9eadf);
    border-radius: 2px;
  }
  .access-point {
    position: absolute;
    left: 876px;
    top: 46px;
    width: 66px;
    height: 404px;
    border-radius: 10px;
    background: linear-gradient(90deg, var(--ap-light), var(--ap-shade));
  }
  .label {
    position: absolute;
    margin: 0;
    text-align: center;
    font-weight: 500;
  }
  .label--computer {
    left: 92px;
    top: 551px;
    width: 240px;
    font-size: 17px;
    color: var(--brand-green);
  }
  .label--ap {
    left: 820px;
    top: 530px;
    width: 170px;
    font-size: 15px;
    line-height: 20px;
    color: var(--paper);
  }
  .troubleshooting {
    position: absolute;
    left: 54px;
    top: 608px;
    width: 760px;
    font-size: 11.5px;
    line-height: 17px;
  }
  .troubleshooting h2 {
    margin: 0 0 7px;
    font-size: 12px;
    font-weight: 600;
  }
  .steps, .steps ul {
    list-style: none;
    margin: 0;
    padding: 0;
  }
  .steps > li {
    position: relative;
    padding-left: 18px;
  }
  .steps > li::before {
    content: "➤";
    position: absolute;
    left: 0;
    top: 0;
  }
  .steps ul li {
    position: relative;
    padding-left: 14px;
  }
  .steps ul li::before {
    content: "➡";
    position: absolute;
    left: 0;
    top: 0;
    font-size: 9px;
  }
  .brand-mark {
    position: absolute;
    left: 837px;
    top: 597px;
    width: 135px;
    height: 135px;
    display: flex;
    align-items: center;
    justify-content: center;
    font-family: "Poppins", sans-serif;
    font-weight: 600;
    font-size: 36px;
    color: var(--paper);
  }
</style>
</head>
<body>
<div class="splash">
  <svg class="backdrop" width="1024" height="768" viewBox="0 0 1024 768" aria-hidden="true">
    <rect class="content-panel" x="0" y="0" width="780" height="595" fill="var(--paper)"/>
    <path class="headline-wave" d="M0 0 H780 V30 C730 30 706 62 684 128 C656 212 620 268 540 268 H0 Z" fill="var(--brand-green)"/>
    <path class="ethernet-cable" d="M348 492 H888 Q905 492 905 475 V448" fill="none" stroke="var(--ink)" stroke-width="3.5" stroke-linecap="round"/>
  </svg>

  <h1 class="headline">Waiting for connection to Wi-Fi access point...</h1>

  <div class="cab-computer" role="img" aria-label="Industrial tractor cab computer showing the KTWG application screen"></div>
  <p class="label label--computer">Tractor Cab Computer</p>

  <div class="access-point" role="img" aria-label="Outdoor Wi-Fi access point with two antennas"></div>
  <p class="label label--ap">Wi-Fi Access<br>Point</p>

  <section class="troubleshooting">
    <h2>Troubleshooting steps:</h2>
    <ul class="steps">
      <li>This screen should only be visible for a short time on boot.</li>
      <li>If this screen stays visible for more than a minute:
        <ul>
          <li>Verify that the Wi-Fi Access Point (AP) powers up when this system does (indicated by a green light on the side of the AP).</li>
          <li>Check the Ethernet cable between this system and the AP for damage, and replace it if necessary.</li>
          <li>Power-cycle this system and wait for it to reboot fully.</li>
          <li>If the issue persists, contact KTWG support for further assistance.</li>
        </ul>
      </li>
    </ul>
  </section>

  <div class="brand-mark">KTWG</div>
</div>
</body>
</html>
```